Stationery and Business Card Design

We need stationary design for our new company lanternfold. Lanternfold is a company that provides city apartment rentals for tourists in Athens We need business cards, letterheads for A4 and A5 and envelopes for A4 A5. The design needs to be modern, friendly and corporate.

Target Market(s)

City Tourists

Industry/Entity Type

Tourism

```html
<!DOCTYPE html>
<html lang="en">
<head>
<meta charset="utf-8">
<title>Lanternfold Business Card</title>
<link rel="stylesheet" href="https://fonts.googleapis.com/css2?family=Raleway:wght@400;500;600&display=swap">
<style>
  :root {
    --bg: #ababab;
    --plum: #83205a;
    --paper: #f7f7f7;
    --ink: #3a3a3a;
    --muted: #555555;
  }
  * { margin: 0; padding: 0; box-sizing: border-box; }
  html, body { width: 1200px; height: 1200px; overflow: hidden; }
  body {
    position: relative;
    background: var(--bg);
    font-family: "Raleway", sans-serif;
  }
  .card {
    position: absolute;
    border-radius: 22px;
    overflow: hidden;
  }
  .card-front {
    left: 238px; top: 117px; width: 714px; height: 420px;
    background: var(--plum);
  }
  .card-back {
    left: 231px; top: 645px; width: 711px; height: 416px;
    background: var(--paper);
  }
  .front-mark {
    position: absolute; left: 302px; top: 114px;
    width: 102px; height: 100px; background: #ffffff;
  }
  .front-name {
    position: absolute; left: 0; right: 0; top: 222px;
    text-align: center; color: #ffffff;
    font-size: 64px; font-weight: 400; letter-spacing: -1px;
  }
  .back-mark {
    position: absolute; left: 138px; top: 73px;
    width: 102px; height: 98px; background: var(--plum);
  }
  .back-name {
    position: absolute; left: 272px; top: 80px;
    color: var(--plum); font-size: 58px; font-weight: 400; letter-spacing: -1px;
  }
  .person {
    position: absolute; right: 395px; top: 260px; text-align: right;
  }
  .person-name { color: var(--plum); font-size: 26px; font-weight: 600; }
  .person-title { color: var(--muted); font-size: 18px; margin-top: 2px; }
  .contact {
    position: absolute; left: 338px; top: 253px; list-style: none;
  }
  .contact li {
    display: flex; align-items: center; height: 24px;
    font-size: 18px; color: var(--ink);
  }
  .contact svg { width: 18px; height: 14px; margin-right: 16px; fill: var(--plum); }
  .divider {
    position: absolute; left: 51px; top: 357px; width: 611px; height: 2px;
    background: var(--plum);
  }
  .address {
    position: absolute; left: 0; right: 0; top: 376px;
    text-align: center; font-size: 18px; color: var(--ink);
  }
</style>
</head>
<body>
  <section class="card card-front">
    <div class="front-mark"></div>
    <div class="front-name">Lanternfold</div>
  </section>

  <section class="card card-back">
    <div class="back-mark"></div>
    <div class="back-name">Lanternfold</div>

    <div class="person">
      <div class="person-name">John Smith</div>
      <div class="person-title">Your Title</div>
    </div>

    <ul class="contact">
      <li>
        <svg viewBox="0 0 18 14" aria-hidden="true"><path d="M1 4 Q9 -1 17 4 L15 6 L12 4.5 L6 4.5 L3 6 Z M4 7 H14 L16 13 H2 Z"/></svg>
        +00 111 222 3333
      </li>
      <li>
        <svg viewBox="0 0 18 14" aria-hidden="true"><circle cx="9" cy="7" r="6.5" fill="none" stroke="#83205a" stroke-width="1.5"/><path d="M2.5 7 H15.5 M9 0.5 V13.5" stroke="#83205a" stroke-width="1.2"/><ellipse cx="9" cy="7" rx="3" ry="6.5" fill="none" stroke="#83205a" stroke-width="1.2"/></svg>
        www.yourwebsite.com
      </li>
      <li>
        <svg viewBox="0 0 18 14" aria-hidden="true"><rect x="1" y="1" width="16" height="12"/><path d="M1 1 L9 8 L17 1 M1 13 L7 6.5 M17 13 L11 6.5" stroke="#f7f7f7" stroke-width="1.3" fill="none"/></svg>
        yourname@yourwebsite.com
      </li>
    </ul>

    <div class="divider"></div>
    <div class="address">Your Long Commercial or business address in 2 line</div>
  </section>
</body>
</html>
```